Business Card Design

Business Card for professional consulting firm working with large financial institutions.

Target Market(s)

Executive buyers

Industry/Entity Type

Banking

Contact Information for Business Card

Mild creativity wanted. Not boring, but do elaborate artwork.

Font styles to use
Serif
Sans Serif

Colors

Designer to choose colors to be used in the design.

Requirements
Must have
• Standard business card features - company name, individual name, telephone, website, email, locations.
Nice to have
• Two colors
Should not have
• too many colors, fancy printing, cartoons.

```html
<!DOCTYPE html>
<html lang="en">
<head>
<meta charset="UTF-8">
<title>Halden Advisory — Business Card</title>
<link rel="stylesheet" href="https://fonts.googleapis.com/css2?family=Open+Sans:wght@400;600;700&display=swap">
<style>
  :root {
    --backdrop: #3a3a3a;
    --card: #1e1e1f;
    --card-edge: #151516;
    --ink: #f2f2f2;
    --ink-soft: #d6d6d6;
    --emboss-light: #3a3a3b;
  }
  * { margin: 0; padding: 0; box-sizing: border-box; }
  html, body {
    width: 799px; height: 1200px; overflow: hidden;
    background: var(--backdrop);
    font-family: "Open Sans", sans-serif;
  }
  .sheet {
    position: relative; width: 799px; height: 1200px;
    display: flex; flex-direction: column; align-items: center;
    justify-content: space-around; padding: 60px 0;
  }
  .card {
    position: relative; width: 640px; height: 366px;
    background: var(--card);
    border-bottom: 3px solid var(--card-edge);
    box-shadow: 0 18px 40px rgba(0,0,0,.45);
  }
  /* Front */
  .card--front { display: flex; align-items: center; justify-content: center; }
  .front-mark {
    display: flex; align-items: center; gap: 14px;
    color: var(--emboss-light);
    font-size: 48px; font-weight: 400; letter-spacing: 1px;
    white-space: nowrap;
  }
  .mark-dot {
    width: 14px; height: 14px; border-radius: 50%;
    background: var(--emboss-light);
  }
  /* Back */
  .back-mark {
    position: absolute; left: 44px; top: 124px;
    display: flex; align-items: center; gap: 10px;
    color: var(--ink); font-size: 28px; font-weight: 400;
    white-space: nowrap;
  }
  .back-mark .mark-dot { width: 10px; height: 10px; background: var(--ink); }
  .holder {
    position: absolute; left: 372px; top: 118px;
    color: var(--ink);
  }
  .holder__name { font-size: 22px; font-weight: 700; line-height: 1.2; }
  .holder__role { font-size: 14px; font-weight: 400; color: var(--ink-soft); }
  .contact {
    position: absolute; left: 330px; top: 205px;
    color: var(--ink); font-size: 15px; line-height: 1.45;
    list-style: none;
  }
  .contact__address { margin-bottom: 6px; padding-left: 30px; }
  .contact__row { display: flex; align-items: center; gap: 14px; }
  .contact__icon { width: 16px; height: 16px; flex: none; fill: var(--ink); }
</style>
</head>
<body>
<main class="sheet">
  <section class="card card--front" aria-label="Card front">
    <div class="front-mark"><span class="mark-dot"></span>Halden Advisory</div>
  </section>

  <section class="card card--back" aria-label="Card back">
    <div class="back-mark"><span class="mark-dot"></span>Halden Advisory</div>
    <div class="holder">
      <p class="holder__name">John Doe Smith</p>
      <p class="holder__role">Managing Director</p>
    </div>
    <ul class="contact">
      <li class="contact__address">234 Anywhere St., Any City,<br>Any Town, US 123456</li>
      <li class="contact__row">
        <svg class="contact__icon" viewBox="0 0 16 16" aria-hidden="true"><path d="M3 1h3l1.5 3.5-2 1.3a9 9 0 0 0 4.7 4.7l1.3-2L15 10v3a2 2 0 0 1-2 2A12 12 0 0 1 1 3a2 2 0 0 1 2-2z"/></svg>
        555.555.5555
      </li>
      <li class="contact__row">
        <svg class="contact__icon" viewBox="0 0 16 16" aria-hidden="true"><path d="M1 3h14v10H1z M2 4l6 5 6-5" fill="none" stroke="#f2f2f2" stroke-width="1.4"/></svg>
        johndoe@example.com
      </li>
      <li class="contact__row">
        <svg class="contact__icon" viewBox="0 0 16 16" aria-hidden="true"><g fill="none" stroke="#f2f2f2" stroke-width="1.2"><circle cx="8" cy="8" r="6.5"/><ellipse cx="8" cy="8" rx="3" ry="6.5"/><path d="M1.5 8h13M2.5 4.8h11M2.5 11.2h11"/></g></svg>
        www.yourwebsite.com
      </li>
    </ul>
  </section>
</main>
</body>
</html>
```